Sell the dream! Property investment proposal document

We are looking for a proposal document which outlines our vision for property development. The purpose of the document is to raise investment from investors - sell the dream!
Brief summary:
Kestrel Dwellings Developments, is an emerging New Zealand property investment company with a focus on providing unique property investment opportunities.
Our expertise and capabilities in architectural modular homes provide us with a remarkable advantage in tackling the development of properties that are typically considered challenging, remote, or uniquely positioned.
Our specialization in this niche sector of property development not only sets us apart from competitors, but also paves the way for lucrative investment opportunities in the New Zealand property market.
Feel free to use any images from www.kestreldwellings.co.nz
Target Market(s)
investors for a unique property development opportunity
Industry/Entity Type
luxury property development in unique locations throughout New Zealand
Colors
Designer to choose only greyscale colors for use in the design.
Look and feel

```html
<!DOCTYPE html>
<html lang="en">
<head>
<meta charset="utf-8">
<title>Kestrel Dwellings Developments – Investment Proposal</title>
<link rel="stylesheet" href="https://fonts.googleapis.com/css2?family=Montserrat:wght@300;400;500&display=swap">
<style>
  :root {
    --backdrop: #ebebeb;
    --page: #2b2b2b;
    --page-top: #1f1f20;
    --ink: #ffffff;
    --ink-soft: #d6d6d6;
    --rule: #5a5a5a;
    --box: #2c2c2c;
    --hatch: #333334;
  }
  * { margin: 0; padding: 0; box-sizing: border-box; }
  html, body { width: 1200px; height: 573px; overflow: hidden; background: var(--backdrop); }
  body { position: relative; font-family: "Montserrat", Arial, sans-serif; color: var(--ink); }

  .page { position: absolute; width: 371px; height: 525px; background: var(--page); overflow: hidden; }
  .page--cover { left: 23px; top: 21px; }
  .page--overview { left: 415px; top: 24px; }
  .page--strengths { left: 810px; top: 24px; }

  .abs { position: absolute; }
  .photo { position: absolute; }

  /* cover */
  .cover-top { left: 0; top: 0; width: 371px; height: 194px; background: var(--page-top); }
  .cover-photo { left: 19px; top: 14px; width: 334px; height: 235px;
    background: linear-gradient(180deg, #b9c6d6 0%, #d4dbe4 35%, #2a2a2c 55%, #1b1b1c 80%, #3a3a3c 100%); }
  .brand-name { left: 0; top: 272px; width: 371px; text-align: center; font-size: 60px; font-weight: 400; letter-spacing: -1px; line-height: 1; }
  .cover-title { left: 0; top: 347px; width: 371px; text-align: center; font-size: 23.5px; font-weight: 400; letter-spacing: 0.5px; }
  .cover-intro { left: 18px; top: 404px; width: 335px; text-align: center; font-size: 7.6px; line-height: 15.5px; font-weight: 400; color: var(--ink-soft); }
  .cover-skyline { left: 0; top: 430px; width: 371px; height: 95px;
    background: linear-gradient(180deg, rgba(43,43,43,0) 0%, #3a3a3b 60%, #454546 100%); }

  /* shared text */
  .heading { font-size: 13.4px; font-weight: 400; letter-spacing: 0.2px; line-height: 1; }
  .body-text { font-size: 5.1px; line-height: 10px; font-weight: 400; color: var(--ink-soft); text-align: justify; }
  .body-text p + p { margin-top: 10px; }

  /* overview page */
  .hatch { background: var(--hatch); }
  .hatch-upper { left: 0; top: 0; width: 186px; height: 248px; }
  .hatch-lower { left: 185px; top: 274px; width: 186px; height: 251px; }
  .team-photo { left: 18px; top: 22px; width: 150px; height: 203px;
    background: linear-gradient(160deg, #e6e9ec 0%, #c9b59c 45%, #6d6a68 75%, #e9e9e9 100%); }
  .meeting-photo { left: 204px; top: 297px; width: 150px; height: 203px;
    background: linear-gradient(170deg, #3a3f46 0%, #6f6a66 40%, #3c4a5e 70%, #1c2430 100%); }
  .overview-heading { left: 206px; top: 26px; }
  .overview-text { left: 206px; top: 45px; width: 147px; }
  .divider { left: 18px; top: 261px; width: 334px; height: 1px; background: var(--rule); }
  .origins-heading { left: 18px; top: 297px; }
  .origins-text { left: 18px; top: 314px; width: 147px; }

  /* strengths page */
  .handshake-photo { left: 19px; top: 22px; width: 334px; height: 144px;
    background: linear-gradient(120deg, #f0f0f0 0%, #9aa7b8 40%, #2f4566 60%, #c5c5c5 100%); }
  .landscape-photo { left: 19px; top: 242px; width: 334px; height: 138px;
    background: linear-gradient(180deg, #eef1f4 0%, #9aa6b0 35%, #6f8a5a 60%, #9bae6b 80%, #d0d0d0 100%); }
  .info-box { position: absolute; left: 28px; width: 314px; background: var(--box); border: 1px solid var(--rule); padding: 8px 14px; text-align: center; }
  .info-box--advantage { top: 129px; height: 87px; }
  .info-box--finance { top: 347px; height: 153px; }
  .info-box .heading { margin-top: 2px; margin-bottom: 8px; }
  .info-box .body-text { text-align: center; }
</style>
</head>
<body>

<section class="page page--cover">
  <div class="abs cover-top"></div>
  <div class="photo cover-photo" role="img" aria-label="Dark modular showroom building under a pale blue sky"></div>
  <div class="abs brand-name">Kestrel</div>
  <h1 class="abs cover-title">WELCOME TO KESTREL</h1>
  <p class="abs cover-intro">Kestrel Dwellings Developments, is an emerging New Zealand property investment company with a focus on providing unique property investment opportunities.</p>
  <div class="abs cover-skyline" role="img" aria-label="Line drawing of the Auckland city skyline"></div>
</section>

<section class="page page--overview">
  <div class="abs hatch hatch-upper" role="img" aria-label="Fine diagonal line pattern"></div>
  <div class="abs hatch hatch-lower" role="img" aria-label="Fine diagonal line pattern"></div>
  <div class="photo team-photo" role="img" aria-label="Three colleagues discussing plans around a laptop in a bright office"></div>

  <h2 class="abs heading overview-heading">BUSINESS OVERVIEW</h2>
  <div class="abs body-text overview-text">
    <p>Kestrel Dwellings Developments, is an emerging New Zealand property investment company with a focus on providing unique property investment opportunities. Our expertise and capabilities in architectural modular homes provide us with a remarkable advantage in tackling the development of properties that are typically considered challenging, remote, or uniquely positioned.</p>
    <p>As a company, with 48 employees boasting a wealth of experience in handling complex architectural projects, making us well-equipped to navigate the intricacies and demands of such ventures. This advantage allows us to not only execute projects efficiently but also to deliver exceptional results within condensed time frames. By capitalizing on our ability to develop difficult, remote, or one-of-a-kind properties swiftly and effectively, Kestrel Dwellings Developments offers investors a rare chance to engage in projects that promise exceptional profitability in the New Zealand property market.</p>
  </div>

  <div class="abs divider"></div>

  <h2 class="abs heading origins-heading">BUSINESS ORIGINS</h2>
  <div class="abs body-text origins-text">
    <p>Kestrel Dwellings Developments was established with the goal of transforming the property investment market in New Zealand by introducing an innovative approach that centers on architectural modular designs and streamlined project timelines. Driven by our enthusiasm for architecture and real estate, we have expanded our successful business model to not only offer financial opportunities for investors but also to expand on our passion for high-end architectural design.</p>
    <p>With a wealth of experience accumulated over the past six years in the construction and the property market, we are pivoting to focus solely on our property development initiatives, presenting completed Kestrel projects to the market, in exclusive locations. These projects will boast high-quality standards, meticulous attention to detail and landscaping, and creative design elements. By introducing completed Kestrel properties into the market, we aim to reach a wider audience catering to individuals who prefer ready-to-occupy homes, over engaging in the design and construction process.</p>
  </div>

  <div class="photo meeting-photo" role="img" aria-label="Two colleagues smiling while reviewing work on a laptop"></div>
</section>

<section class="page page--strengths">
  <div class="photo handshake-photo" role="img" aria-label="Business handshake across a meeting table"></div>
  <div class="info-box info-box--advantage">
    <h2 class="heading">COMPETITIVE ADVANTAGE</h2>
    <p class="body-text">Our competitive advantage lies in the uniqueness of our property investment opportunities. Unlike traditional real estate companies, we focus on offering properties that are not only profitable but also aesthetically pleasing and unique. By catering to the tastes of architecture lovers, we set ourselves apart from the competition and attract a niche market of customers who appreciate the artistry and design of our projects. Additionally, the streamlined and condensed timelines facilitated by our modular approach provide quicker returns on investment.</p>
  </div>

  <div class="photo landscape-photo" role="img" aria-label="View from a glass-walled home over green hills and a harbour"></div>
  <div class="info-box info-box--finance">
    <h2 class="heading">FINANCIAL SUMMARY</h2>
    <div class="body-text">
      <p>In terms of financial projections, with each development, we anticipate a profit of 10%-20% which will be project dependent. This growth is fueled by the increasing demand for unique property investments in New Zealand and our ability to deliver high-quality services to the market in a condensed time frame, with heavily controlled costs. With a solid business model and a dedicated team, we are confident in our ability to achieve success and establish Kestrel Dwellings Investments as a trusted name in the industry. New Zealand's property market has been experiencing steady growth over the years, making it an attractive destination for property investors.</p>
      <p>With its beautiful landscapes and strong economy, New Zealand offers a diverse range of investment opportunities for both local and international investors. The demand for quality properties in prime locations continues to rise, creating a favorable environment for property investment companies like ours that can lean on our modular benefits of being able to reach unique and remote locations.</p>
    </div>
  </div>
</section>

</body>
</html>
```